Website Design for Employee Moral and Happiness Company

Looking for a clean website design that explains our features in a step by step manner so our visitors know exactly what our site does before logging in.

The site is called "Velrato". See logo design and video for a sample of style and an overview of what we do.

Target Market(s)

Business owners that are looking to retain employees.

Number of Pages Required

1 page

```html
<!DOCTYPE html>
<html lang="en">
<head>
<meta charset="utf-8">
<title>Velrato — Testimonials</title>
<link href="https://fonts.googleapis.com/css2?family=Merriweather:wght@700&family=Nunito:wght@400;600;700;800&display=swap" rel="stylesheet">
<style>
  :root {
    --header-bg: #e8dfd5;
    --panel-bg: #e4dccb;
    --accent: #e85f08;
    --button: #ff6a00;
    --ink: #2e2e2e;
    --muted: #6f6a63;
    --arrow: #5a4f42;
    --navy: #283a5b;
    --navy-soft: #3a4d70;
    --quote-mark: #c5baab;
  }
  * { margin: 0; padding: 0; box-sizing: border-box; }
  html, body { width: 1200px; height: 698px; overflow: hidden; }
  body { font-family: "Nunito", sans-serif; background: var(--panel-bg); position: relative; }

  .site-header {
    position: absolute; top: 0; left: 0; width: 1200px; height: 89px;
    background: var(--header-bg); border-bottom: 1px solid #efe8de;
  }
  .brand {
    position: absolute; left: 66px; top: 20px;
    font-weight: 800; font-size: 38px; line-height: 46px;
    color: #111; display: flex; align-items: center; gap: 8px;
  }
  .brand-dot { width: 12px; height: 12px; border-radius: 50%; background: var(--accent); }
  .main-nav { position: absolute; top: 34px; left: 0; width: 900px; height: 20px; }
  .main-nav a { position: absolute; top: 0; font-size: 15.5px; line-height: 20px; color: var(--ink); text-decoration: none; white-space: nowrap; }
  .main-nav a.is-active { color: var(--accent); text-decoration: underline; text-underline-offset: 4px; }
  .nav-home { left: 278px; }
  .nav-events { left: 342px; }
  .nav-intro { left: 499px; }
  .nav-why { left: 654px; }
  .nav-testimonials { left: 767px; }
  .login { position: absolute; left: 906px; top: 34px; font-size: 15.5px; line-height: 20px; color: var(--ink); display: flex; align-items: center; gap: 10px; }
  .signup {
    position: absolute; left: 995px; top: 18px; width: 141px; height: 45px;
    background: var(--button); color: #fff; border-radius: 23px;
    font-weight: 800; font-size: 16px; display: flex; align-items: center; justify-content: center;
  }

  .testimonials { position: absolute; top: 90px; left: 0; width: 762px; height: 608px; background: var(--panel-bg); overflow: hidden; }
  .section-title {
    position: absolute; top: 76px; left: 0; width: 832px; text-align: center;
    font-family: "Merriweather", serif; font-weight: 700; font-size: 32px; line-height: 40px; color: #333;
  }
  .quote-mark { position: absolute; left: 616px; top: 385px; width: 160px; height: 145px; border-radius: 70px 40px 20px 60px; background: var(--quote-mark); opacity: 0.6; }
  .quote-text {
    position: absolute; top: 170px; left: 148px; width: 536px;
    text-align: center; font-size: 18.5px; line-height: 34px; color: var(--muted);
  }
  .quote-author { position: absolute; top: 364px; left: 0; width: 832px; text-align: center; font-weight: 700; font-size: 18.5px; line-height: 24px; color: #25262b; letter-spacing: 0.3px; }
  .slider-arrow { position: absolute; top: 233px; }
  .slider-arrow.prev { left: 84px; }
  .slider-arrow.next { left: 718px; }

  .feature-panel { position: absolute; top: 90px; left: 762px; width: 438px; height: 608px; background: var(--accent); }
  .feature-art {
    position: absolute; left: 62px; top: 181px; width: 262px; height: 208px;
    border-radius: 12px;
    background: linear-gradient(160deg, var(--navy-soft), var(--navy));
  }
  .progress { position: absolute; left: 403px; top: 175px; width: 20px; height: 256px; }
  .progress-label { position: absolute; left: 322px; top: 338px; font-size: 11.5px; line-height: 16px; font-weight: 700; color: #fff; white-space: nowrap; }
</style>
</head>
<body>
  <header class="site-header">
    <div class="brand"><span>Velrato</span><span class="brand-dot"></span></div>
    <nav class="main-nav">
      <a href="#" class="nav-home is-active">Home</a>
      <a href="#" class="nav-events">Boring Work Events</a>
      <a href="#" class="nav-intro">Introducing Velrato</a>
      <a href="#" class="nav-why">Why Velrato</a>
      <a href="#" class="nav-testimonials">Testimonials</a>
    </nav>
    <div class="login">
      <svg width="12" height="12" viewBox="0 0 12 12" fill="none" stroke="#2e2e2e" stroke-width="1.3"><path d="M1 6h7M5 3l3 3-3 3M10 1v10"/></svg>
      Login
    </div>
    <div class="signup">SIGN UP</div>
  </header>

  <section class="testimonials">
    <h2 class="section-title">Testimonials</h2>
    <div class="quote-mark" role="img" aria-label="Large decorative closing quotation mark"></div>
    <p class="quote-text">These guys are great from beginning to end. Very professional, excellent businessmen, hard workers, and top-quality work. Excellent communication, do what they say they will do and more, and really go the extra mile to make the job as painless as possible. Without reservations would</p>
    <p class="quote-author">RANDOM USER - ABC ORGANIZATION</p>
    <svg class="slider-arrow prev" width="30" height="50" viewBox="0 0 30 50"><path d="M24 4L8 25l16 21" fill="none" stroke="var(--arrow)" stroke-width="6"/></svg>
    <svg class="slider-arrow next" width="30" height="50" viewBox="0 0 30 50"><path d="M6 4l16 21L6 46" fill="none" stroke="var(--arrow)" stroke-width="6"/></svg>
  </section>

  <aside class="feature-panel">
    <div class="feature-art" role="img" aria-label="Illustration: speech bubble with hand lettering reading Boost employee morale"></div>
    <svg class="progress" width="20" height="256" viewBox="0 0 20 256">
      <line x1="10" y1="6" x2="10" y2="250" stroke="#fff" stroke-width="1.5"/>
      <g fill="var(--accent)" stroke="#fff" stroke-width="1.5">
        <circle cx="10" cy="6" r="5.5"/><circle cx="10" cy="47" r="5.5"/><circle cx="10" cy="88" r="5.5"/>
        <circle cx="10" cy="130" r="5.5"/><circle cx="10" cy="212" r="5.5"/><circle cx="10" cy="250" r="5.5"/>
      </g>
      <circle cx="10" cy="171" r="10" fill="#f3a46e"/>
      <circle cx="10" cy="171" r="6" fill="#fff"/>
    </svg>
    <span class="progress-label">Testimonials</span>
  </aside>
</body>
</html>
```